Start-Up für Training, Coaching & Consulting sucht modernes Webdesign!
Zielgruppe
Wer ist TAVI Training, Coaching & Consulting?
Wir führen Führungskräftetrainings durch, machen Privatkunden für Bewerbungen fit und unterstützen Unternehmen mit Verkaufstrainings. Wir entwickeln Persönlichkeiten im Coaching. Wir beraten Unternehmen und helfen ihnen dabei, ihre Geschäftsabläufe und Prozesse zu optimieren. Dabei steht unsere hohe Qualität im Mittelpunkt - gemeinsam mit unseren kreativen Trainingsmethoden. Unser Background (Diplom-Kaufleute und geprüfte Trainer) bietet dafür die passende Ausgangslage.
Was bedeutet TAVI?
Tavi ist Maori und bdeutet Kreis/Spirale. Er symbolisiert einen wachsenden Silberfarn und steht für persönliche Entwicklung und Entfaltung. Der Tavi ist einerseits unser Namensgeber und unser Logo, andererseits steht der Tavi aber auch für unsere Werte: Denn wir wollen unseren Kunden dabei helfen zu wachsen und sich weiterzuentwickeln - und dies auf eine hochqualitative und seriöse Art und Weise ohne den Eindruck von Esoterik oder Erlebnispädagogik zu vermitteln.
Aufgabenstellung
Modernes Design, das unsere Philosophie widerspiegelt: Wir möchten unseren Kunden auf seriöse und hochqualitative Weise weiterentwickeln. Wir stehen für nachhaltigen Lernerfolg, kreative Trainingsmethoden, Abwechslung, Spaß am Lernen, Qualität, Kompetenz, Fachwissen und Dynamik.
Layout:
1) Header: QMSR geprüfter Trainer, Menüpunkte (siehe Architektur)
2) Banner
3) 3 Teaser (Training, Coaching, Consulting) + Header + 2-3 Zeilen Text (+Icons)
>>> Sichtbarer Bereich auf Homepage: Menü, Banner, Teaser
4) "Warum Sie uns wählen sollten": 5 bullet points ohne weiteren Text
5) "Aus unserem Blog": Frame für 3 Blogartikel + Bild + Datum + Header + 2-3 Zeilen Text
6) Alle drei QMSR Logos
7) Footer: Click Us (quick links), Contact Us (Adresse), Follow Us (Pinnwald, ZOLP, Kontaktor)
8) Copyright + Impressum
>>> Das Design soll klar sein, aber nicht zu kantig. Vielmehr sollen abgerundete Ecken und dynamische Elemente genutzt werden.
Architektur:
3 Ebenen:
1) Homepage
2) TAVI, Training, Coaching, Consulting, für Trainer, Kundenstimmen/Referenzen, Kontakt
3) noch zu bestimmende Produktdetailseiten
Texte werden noch erstellt, Layout kann ggf. mit Platzhaltertext gefüllt werden.
Bildmaterial: Logo und vorhandenes Imagebild werden zur Verfügung gestellt. Bilder können ggf. gekauft werden. Vorschläge erwünscht.
Corporate colors:
grün: #a2c61b + monochromatic colors
http://www.tintoskop.de/a2c61b
grau: #474747 + monochromatic colors
http://www.tintoskop.de/474747

```html
<!DOCTYPE html>
<html lang="de">
<head>
<meta charset="utf-8">
<title>TAVI Training, Coaching & Consulting</title>
<link rel="stylesheet" href="https://fonts.googleapis.com/css2?family=Raleway:wght@300;400;500;700&family=Montserrat:wght@400;500&display=swap">
<style>
:root{
  --green:#a2c61b;
  --green-dark:#7fa012;
  --green-light:#c9e05a;
  --cream:#eef3cf;
  --charcoal:#2c2f33;
  --charcoal-deep:#25282b;
  --text:#3a3a3a;
  --text-soft:#6a6a6a;
  --footer-text:#c8c8c8;
  --footer-muted:#8a8d90;
  --white:#ffffff;
  --badge-blue:#1f5aa8;
}
*{box-sizing:border-box;margin:0;padding:0}
html,body{width:789px;height:1200px;overflow:hidden;background:var(--white)}
.page{position:relative;width:789px;height:1200px;overflow:hidden;font-family:"Raleway",sans-serif;color:var(--text)}
.abs{position:absolute}
.backdrop{position:absolute;left:0;top:0}

/* header */
.site-header{position:absolute;left:0;top:0;width:789px;height:51px;background:var(--charcoal)}
.brand{position:absolute;left:124px;top:10px;color:var(--white);font-family:"Raleway",sans-serif;font-weight:700;font-size:24px;letter-spacing:1px;line-height:26px;display:flex;align-items:center;gap:6px}
.brand-dot{width:10px;height:10px;border-radius:50%;background:var(--green)}
.brand-tagline{position:absolute;left:124px;top:37px;font-size:5px;color:#bbb;letter-spacing:.3px}
.nav{position:absolute;top:0;left:269px;height:51px;display:flex;align-items:center;font-family:"Montserrat",sans-serif;font-size:8.4px;color:var(--white)}
.nav-item{display:flex;align-items:center;height:51px;padding:0 9px}
.nav-item.active{background:#25282b;color:var(--green);border-bottom:2px solid var(--green)}
.nav-sep{padding:0 4px;color:#ccc}
.caret{width:6px;height:6px;margin-left:4px}
.header-badge{position:absolute;left:679px;top:19px;width:67px;height:19px;background:var(--badge-blue);border-radius:2px}

/* hero */
.hero-photo{position:absolute;left:0;top:51px;width:789px;height:290px;background:radial-gradient(ellipse at 70% 40%,#9bc24a 0%,#6f9c2c 45%,#44701a 100%)}
.hero-title{position:absolute;left:113px;top:98px;color:var(--white);font-weight:300;font-size:25px;line-height:30px;letter-spacing:.3px}
.hero-title strong{font-weight:700}
.hero-chevron{position:absolute;left:98px;top:105px;width:11px;height:16px}
.hero-lead{position:absolute;left:113px;top:157px;color:var(--white);font-size:12.4px;line-height:17px;font-weight:400}
.btn-more{position:absolute;left:111px;top:203px;width:99px;height:33px;border-radius:17px;background:var(--green);color:var(--white);font-family:"Montserrat",sans-serif;font-size:8px;font-weight:500;display:flex;align-items:center;justify-content:center;letter-spacing:.3px}
.slider-arrow{position:absolute;top:150px;width:28px;height:46px}

/* teasers */
.teaser{position:absolute;top:339px;width:160px;text-align:center}
.teaser-photo{width:134px;height:134px;margin:0 auto;border-radius:50%;border:4px solid var(--green);background:linear-gradient(135deg,#dfe3e8,#8c99a6)}
.teaser-title{margin-top:23px;font-family:"Montserrat",sans-serif;font-size:9.6px;font-weight:500;color:#222;letter-spacing:.2px}
.teaser-rule{margin:6px auto 0;width:141px;border-top:1px dotted #999}
.teaser-text{margin-top:6px;font-size:7.2px;line-height:12.6px;color:var(--text)}

.divider{position:absolute;left:110px;width:576px;height:1px;background:#cfdc92}

/* why */
.section-title{position:absolute;color:var(--green);font-size:17.5px;font-weight:500;letter-spacing:.3px}
.section-rule{position:absolute;border-top:1px dotted #c3d27a}
.why-list{position:absolute;left:98px;top:657px;list-style:none;color:var(--green);font-size:12.6px;line-height:25.3px}
.why-list li::before{content:"› ";}

/* blog */
.blog-item{position:absolute;left:489px;width:196px;height:62px}
.blog-thumb{position:absolute;left:0;top:0;width:40px;height:40px;border-radius:50%;border:3px solid var(--green);background:linear-gradient(135deg,#e3e6ea,#7f8c98)}
.blog-text{position:absolute;left:54px;top:-4px;width:142px;font-size:6.7px;line-height:12.6px;color:var(--text-soft)}
.blog-more{color:var(--green)}
.blog-rule{position:absolute;left:489px;width:196px;border-top:1px dotted #a9bf4b}

/* partner badges */
.partner{position:absolute;top:931px;height:22px;background:var(--badge-blue);border-radius:2px}

/* footer */
.footer-links{position:absolute;left:106px;top:1036px;list-style:none;font-size:8.6px;line-height:15.8px;color:var(--footer-text);font-family:"Montserrat",sans-serif}
.contact-col{position:absolute;top:1036px;font-size:6.7px;line-height:12.6px;color:var(--footer-muted)}
.contact-label{color:var(--green);font-size:8.6px;line-height:12px;margin-bottom:1px}
.contact-icon{position:absolute;top:1037px;width:13px;height:11px}
.follow-label{position:absolute;left:600px;top:1036px;font-size:8.6px;color:var(--footer-text);letter-spacing:.3px}
.social{position:absolute;top:1053px;width:23px;height:23px;border-radius:50%;background:var(--green)}
.footer-rule{position:absolute;left:71px;top:1126px;width:655px;border-top:1px dotted #5c6064}
.copyright{position:absolute;left:0;top:1143px;width:789px;text-align:center;font-size:8px;line-height:12.6px;color:var(--footer-muted)}
</style>
</head>
<body>
<div class="page">

  <div class="hero-photo" role="img" aria-label="Foto: junge Farnwedel mit eingerollter Spirale im Gegenlicht"></div>

  <svg class="backdrop" width="789" height="1200" viewBox="0 0 789 1200" aria-hidden="true">
    <defs>
      <linearGradient id="creamFade" x1="0" y1="0" x2="0" y2="1">
        <stop offset="0" stop-color="#eef3cf"/>
        <stop offset="0.7" stop-color="#f6f8e6"/>
        <stop offset="1" stop-color="#ffffff"/>
      </linearGradient>
      <linearGradient id="bandGreen" x1="0" y1="0" x2="1" y2="0">
        <stop offset="0" stop-color="#9cc21a"/>
        <stop offset="1" stop-color="#b4d62a"/>
      </linearGradient>
      <linearGradient id="lowerFade" x1="0" y1="0" x2="0" y2="1">
        <stop offset="0" stop-color="#ffffff"/>
        <stop offset="1" stop-color="#eef3cf"/>
      </linearGradient>
    </defs>
    <path d="M0 264 C150 280 400 330 520 310 C640 290 740 240 789 205 L789 600 L0 600 Z" fill="url(#bandGreen)"/>
    <path d="M0 285 C200 300 420 332 520 326 C640 318 740 275 789 238 L789 560 L0 560 Z" fill="url(#creamFade)"/>
    <rect x="0" y="560" width="789" height="320" fill="#ffffff"/>
    <rect x="0" y="880" width="789" height="80" fill="url(#lowerFade)"/>
    <path d="M0 943 C200 950 420 930 600 915 C700 905 760 895 789 885 L789 1200 L0 1200 Z" fill="url(#bandGreen)"/>
    <path d="M0 967 C200 968 420 1010 540 1010 C650 1010 740 975 789 950 L789 1200 L0 1200 Z" fill="var(--charcoal)"/>
  </svg>

  <header class="site-header">
    <div class="brand">TAVI<span class="brand-dot"></span></div>
    <div class="brand-tagline">Training • Coaching • Consulting</div>
    <nav class="nav">
      <span class="nav-item active">HOME</span>
      <span class="nav-sep">I</span>
      <span class="nav-item">ÜBER UNS
        <svg class="caret" viewBox="0 0 6 6"><path d="M0.5 1.5 L3 4.3 L5.5 1.5" stroke="#a2c61b" stroke-width="1.4" fill="none"/></svg></span>
      <span class="nav-sep">I</span>
      <span class="nav-item">FÜR TRAINERS
        <svg class="caret" viewBox="0 0 6 6"><path d="M0.5 1.5 L3 4.3 L5.5 1.5" stroke="#a2c61b" stroke-width="1.4" fill="none"/></svg></span>
      <span class="nav-sep">I</span>
      <span class="nav-item">REFERENZEN</span>
      <span class="nav-sep">I</span>
      <span class="nav-item">KONTAKT</span>
    </nav>
    <div class="header-badge" role="img" aria-label="Abzeichen geprüfter Business-Trainer"></div>
  </header>

  <svg class="hero-chevron" viewBox="0 0 11 16" aria-hidden="true"><path d="M2 2 L8 8 L2 14" stroke="#a2c61b" stroke-width="2.6" fill="none"/></svg>
  <h1 class="hero-title">TRAINING, COACHING<br>CONSULTING <strong>FÜR TRAINER</strong></h1>
  <p class="hero-lead">Lorem ipsum dolor sit amet consectetur adipiscing elit.<br>Aliquam vehicula, mauris non</p>
  <div class="btn-more">MEHR ERFAHREN</div>
  <svg class="slider-arrow" style="left:17px" viewBox="0 0 28 46" aria-label="Zurück"><path d="M22 4 L6 23 L22 42" stroke="#fff" stroke-width="6" fill="none" stroke-linecap="round" stroke-linejoin="round"/></svg>
  <svg class="slider-arrow" style="left:738px" viewBox="0 0 28 46" aria-label="Weiter"><path d="M6 4 L22 23 L6 42" stroke="#fff" stroke-width="6" fill="none" stroke-linecap="round" stroke-linejoin="round"/></svg>

  <div class="teaser" style="left:127px">
    <div class="teaser-photo" role="img" aria-label="Foto: gefaltete Hände auf einem Schreibtisch"></div>
    <h2 class="teaser-title">LOREM IPSUM DOLOR SIT</h2>
    <div class="teaser-rule"></div>
    <p class="teaser-text">Lorem ipsum dolor sit amet, consectetur<br>adipiscing elit. In dapibus accumsan luctus.</p>
  </div>
  <div class="teaser" style="left:311px">
    <div class="teaser-photo" role="img" aria-label="Foto: zwei Geschäftsleute schauen gemeinsam auf ein Tablet"></div>
    <h2 class="teaser-title">ADIPISCING ELIT</h2>
    <div class="teaser-rule"></div>
    <p class="teaser-text">Dolor sit amet, consectetur adipiscing elit.<br>In dapibus accumsan luctus.</p>
  </div>
  <div class="teaser" style="left:494px">
    <div class="teaser-photo" role="img" aria-label="Foto: Hände mit Stift und Tablet in einer Besprechung"></div>
    <h2 class="teaser-title">ELIT NON VEHICULA</h2>
    <div class="teaser-rule"></div>
    <p class="teaser-text">Sit amet, consectetur adipiscing elit. In<br>dapibus accumsan luctus.</p>
  </div>

  <div class="divider" style="top:579px"></div>

  <h2 class="section-title" style="left:106px;top:609px">WHY CHOOSE US</h2>
  <div class="section-rule" style="left:106px;top:639px;width:295px"></div>
  <ul class="why-list">
    <li>Vestibulum nec mauris facilisis</li>
    <li>Curabitur et tristique diam, nec sagittis nibh.</li>
    <li>Denim nec sagittis nibh.</li>
    <li>Vestibulum nec mauris facilisis,</li>
    <li>Tristique diam nec lorem</li>
  </ul>

  <h2 class="section-title" style="left:492px;top:604px">BLOG</h2>
  <div class="section-rule" style="left:492px;top:634px;width:189px"></div>

  <article class="blog-item" style="top:661px">
    <div class="blog-thumb" role="img" aria-label="Foto: Geschäftsleute im Gespräch"></div>
    <p class="blog-text">Lorem ipsum dolor sit amet, consectetur adipiscing elit. In dapibus accumsan luctus. Aliquam posuere eros sed nibh sagittis,<br><span class="blog-more">more ›</span></p>
  </article>
  <div class="blog-rule" style="top:716px"></div>
  <article class="blog-item" style="top:728px">
    <div class="blog-thumb" role="img" aria-label="Foto: Geschäftsmann mit Brille"></div>
    <p class="blog-text">Pellentesque habitant morbi tristique senectus et netus et malesuada fames ac turpis egestas.<br><span class="blog-more">more ›</span></p>
  </article>
  <div class="blog-rule" style="top:785px"></div>
  <article class="blog-item" style="top:797px">
    <div class="blog-thumb" role="img" aria-label="Foto: Hände mit Tablet"></div>
    <p class="blog-text">Mauris sollicitudin felis aliquam ipsum dictum vehicula. Donec feugiat sapien nunc, quis auctor libero finibus in.<br><span class="blog-more">more ›</span></p>
  </article>
  <div class="blog-rule" style="top:852px"></div>

  <div class="divider" style="top:884px"></div>

  <div class="partner" style="left:276px;width:67px;top:932px;height:19px" role="img" aria-label="Abzeichen geprüfter Business-Trainer"></div>
  <div class="partner" style="left:372px;width:45px;height:25px" role="img" aria-label="Abzeichen Verbandsmitglied"></div>
  <div class="partner" style="left:449px;width:24px;height:25px" role="img" aria-label="Abzeichen Berufsverband für Trainer, Berater und Coaches"></div>

  <ul class="footer-links">
    <li>HOME</li><li>ÜBER UNS</li><li>FÜR TRAINERS</li><li>REFERENZEN</li><li>KONTAKT</li>
  </ul>

  <svg class="contact-icon" style="left:202px" viewBox="0 0 13 11" aria-hidden="true"><path d="M6.5 0.5 L12.5 5.5 L11 5.5 L11 10.5 L8 10.5 L8 7 L5 7 L5 10.5 L2 10.5 L2 5.5 L0.5 5.5 Z" fill="#a2c61b"/></svg>
  <div class="contact-col" style="left:228px">
    <div class="contact-label">Address</div>
    Vestibulum nec mauris 62<br>Suscipit est et<br>62134 Townname
  </div>

  <svg class="contact-icon" style="left:333px;width:11px" viewBox="0 0 11 11" aria-hidden="true"><rect x="0" y="0" width="11" height="11" rx="2" fill="#a2c61b"/><path d="M3 2.5 C3 6 5 8.5 8.5 8.5 L8.5 7 L7 6.3 L6.3 7 C5 6.5 4.5 6 4 4.7 L4.7 4 L4 2.5 Z" fill="#2c2f33"/></svg>
  <div class="contact-col" style="left:359px">
    <div class="contact-label">Phone</div>
    (000 &nbsp;123 &nbsp;7658 903<br>(000 &nbsp;123 &nbsp;7658 903<br>(000 &nbsp;123 &nbsp;7658 903
  </div>

  <svg class="contact-icon" style="left:451px" viewBox="0 0 13 11" aria-hidden="true"><rect x="0" y="1" width="13" height="9" rx="1" fill="#a2c61b"/><path d="M0.5 1.5 L6.5 6 L12.5 1.5" stroke="#2c2f33" stroke-width="1.2" fill="none"/></svg>
  <div class="contact-col" style="left:477px">
    <div class="contact-label">Email</div>
    info@tavi-coaching.de<br>adresse@tavi-coaching.de<br>kontakt@tavi-coaching.de
  </div>

  <div class="follow-label">BITTE FOLGEN</div>
  <div class="social" style="left:592px" role="img" aria-label="Pinnwald"></div>
  <div class="social" style="left:620px" role="img" aria-label="Zwitscherei"></div>
  <div class="social" style="left:648px" role="img" aria-label="Kontaktor"></div>

  <div class="footer-rule"></div>
  <p class="copyright">Aliquam at pulvinar mi. Nulla eget bibendum nisl. Integer consectetur quam ac purus pharetra pulvinar.<br>Aenean faucibus tortor ac tortor aliquet tincidunt. Mauris eget maximus urna.</p>

</div>
</body>
</html>
```